Boutique custom software development company needs new business card

Our nearly 20 year old custom software development company would like to better include the fact that we are now providing Bitcoin services. These new services are B2B include education (how to acquire and securely hold Bitcoin) and integrating Bitcoin payments into existing ecommerce sites or other existing systems. Please keep the card clean and simple. Attached is our current design and some other files. vextorial.com

Target Market(s)

businesses owners interested in long term relationship

Industry/Entity Type

Custom software development and Bitcoin

Contact Information for Business Card

Dale Parker, dale@vextorial.com, vextorial.com, (888) 555-VXTRL

Font styles to use
Other font styles liked:
• monospace

Requirements
Must have
• double-sided
Nice to have
• clean and simple
Should not have
• physical address

```html
<!DOCTYPE html>
<html lang="en">
<head>
<meta charset="utf-8">
<title>Vextorial business card</title>
<link rel="stylesheet" href="https://fonts.googleapis.com/css2?family=Montserrat:wght@400;700;800&display=swap">
<style>
  :root {
    --backdrop: #3b3b3b;
    --card: #121212;
    --card-back: #161616;
    --pattern-dark: #0c0c0c;
    --pattern-mid: #232323;
    --brand-blue: #3f78c6;
    --brand-orange: #f07f1f;
    --ink-light: #e8e8e8;
    --divider: #3f78c6;
  }
  * { box-sizing: border-box; margin: 0; padding: 0; }
  html, body {
    width: 1200px; height: 801px; overflow: hidden;
    background: var(--backdrop);
    font-family: "Montserrat", sans-serif;
  }
  .stage {
    width: 1200px; height: 801px;
    display: flex; align-items: center; justify-content: center; gap: 40px;
  }
  .card {
    position: relative;
    width: 540px; height: 309px;
    border-bottom: 3px solid var(--brand-blue);
    border-left: 2px solid var(--brand-blue);
    overflow: hidden;
  }
  .card--front { background: var(--card); }
  .wordmark {
    position: absolute; left: 48px; top: 62px;
    font-weight: 800; font-size: 46px; letter-spacing: 1px;
    color: var(--brand-blue); line-height: 1;
  }
  .tagline {
    position: absolute; left: 50px; top: 114px;
    font-weight: 400; font-size: 16px; color: var(--brand-blue);
    white-space: nowrap;
  }
  .holder-name {
    position: absolute; left: 50px; top: 232px;
    font-weight: 700; font-size: 19px; letter-spacing: 1px;
    color: var(--brand-blue); text-transform: uppercase;
  }
  .divider {
    position: absolute; left: 262px; top: 170px;
    width: 1px; height: 70px; background: var(--divider);
  }
  .contact-list {
    position: absolute; left: 282px; top: 170px;
    list-style: none;
  }
  .contact-list li {
    display: flex; align-items: center; gap: 10px;
    font-size: 14px; color: var(--ink-light);
    height: 23px; white-space: nowrap;
  }
  .contact-list svg { width: 13px; height: 13px; flex: none; }
  .card--back {
    background: var(--card-back);
    display: flex; align-items: center; justify-content: center;
  }
  .back-pattern {
    position: absolute; inset: 0;
    background: linear-gradient(135deg, var(--pattern-dark) 0%, var(--pattern-mid) 55%, var(--pattern-dark) 100%);
  }
  .back-mark {
    position: relative;
    display: flex; align-items: center; gap: 12px;
  }
  .back-mark__square {
    width: 34px; height: 34px; background: var(--brand-blue);
  }
  .back-mark__name {
    font-weight: 800; font-size: 28px; letter-spacing: 1px;
    color: var(--brand-blue);
  }
</style>
</head>
<body>
<main class="stage">
  <section class="card card--front" aria-label="Card front">
    <div class="wordmark">VEXTORIAL</div>
    <div class="tagline">custom applications &amp; bitcoin services</div>
    <div class="divider"></div>
    <ul class="contact-list">
      <li>
        <svg viewBox="0 0 16 16" aria-hidden="true"><path fill="#f07f1f" d="M3 1h3l1.5 4-2 1.5a9 9 0 0 0 4 4L11 8.5l4 1.5v3a2 2 0 0 1-2 2A12 12 0 0 1 1 3a2 2 0 0 1 2-2z"/></svg>
        (888) 555-VXTRL
      </li>
      <li>
        <svg viewBox="0 0 16 16" aria-hidden="true"><rect x="1" y="3" width="14" height="10" fill="#f07f1f"/><path d="M1 3l7 6 7-6" fill="none" stroke="#121212" stroke-width="1.5"/></svg>
        dale@vextorial.com
      </li>
      <li>
        <svg viewBox="0 0 16 16" aria-hidden="true"><circle cx="8" cy="8" r="7" fill="#f07f1f"/><path d="M1 8h14M8 1c-3 3-3 11 0 14M8 1c3 3 3 11 0 14" fill="none" stroke="#121212" stroke-width="1"/></svg>
        www.vextorial.com
      </li>
    </ul>
    <div class="holder-name">Dale Parker</div>
  </section>

  <section class="card card--back" aria-label="Card back">
    <div class="back-pattern" role="img" aria-label="Repeating tone-on-tone brand pattern in glossy black"></div>
    <div class="back-mark">
      <span class="back-mark__square"></span>
      <span class="back-mark__name">VEXTORIAL</span>
    </div>
  </section>
</main>
</body>
</html>
```